Harbor Loom Floors Letterhead

Letterhead used for business reasons. It must be editable and easy to use.

Address is 2715 W. Pelican Lane Brightwater GA 34187 - 555.382.6519

```html
<!DOCTYPE html>
<html lang="en">
<head>
<meta charset="UTF-8">
<title>Harbor Loom Floors Letterhead</title>
<link href="https://fonts.googleapis.com/css2?family=Lato:wght@400;700&family=Montserrat:wght@400&family=Kaushan+Script&display=swap" rel="stylesheet">
<style>
  :root {
    --backdrop: #e9e6e2;
    --paper: #ffffff;
    --ink: #1d1d1d;
    --brand-orange: #e08a26;
    --brand-grey: #958d87;
    --footer-text: #f2efec;
  }
  html, body {
    margin: 0;
    padding: 0;
    width: 1200px;
    height: 1141px;
    overflow: hidden;
    background: var(--backdrop);
  }
  .letterhead {
    position: absolute;
    left: 218px;
    top: 30px;
    width: 764px;
    height: 1080px;
    background: var(--paper);
    box-shadow: 0 2px 10px rgba(0,0,0,0.12);
    font-family: "Lato", sans-serif;
    color: var(--ink);
  }
  .brand-name {
    position: absolute;
    left: 38px;
    top: 56px;
    width: 170px;
    margin: 0;
    font-family: "Lato", sans-serif;
    font-weight: 400;
    font-size: 30px;
    line-height: 1.12;
    color: var(--brand-orange);
  }
  .sender-address {
    position: absolute;
    right: 37px;
    top: 88px;
    margin: 0;
    font-family: "Montserrat", sans-serif;
    font-style: normal;
    font-size: 13.5px;
    line-height: 18px;
    text-align: right;
  }
  .letter-body {
    position: absolute;
    left: 38px;
    right: 37px;
    top: 290px;
    font-size: 15.2px;
    line-height: 18px;
  }
  .letter-body p { margin: 0; }
  .letter-date { margin-bottom: 20px !important; }
  .recipient { margin-bottom: 31px !important; }
  .recipient-company { margin-bottom: 36px !important; }
  .salutation {
    margin: 0 0 38px;
    font-weight: 700;
    font-size: 18.5px;
    line-height: 22px;
  }
  .paragraph {
    text-align: justify;
    line-height: 16.6px;
    margin-bottom: 18px !important;
  }
  .closing { margin-top: 34px !important; }
  .signature {
    margin-top: 50px !important;
    font-family: "Kaushan Script", cursive;
    font-size: 32px;
    line-height: 1;
  }
  .footer-band {
    position: absolute;
    left: 0;
    top: 1048px;
    width: 764px;
    height: 20px;
  }
  .footer-phone {
    font-family: "Montserrat", sans-serif;
    font-size: 13px;
    fill: var(--footer-text);
  }
</style>
</head>
<body>
  <main class="letterhead">
    <h1 class="brand-name">Harbor Loom Floors</h1>

    <address class="sender-address">
      2715 W. Pelican Lane<br>
      Brightwater GA 34187
    </address>

    <section class="letter-body">
      <p class="letter-date">January-03-2020</p>

      <p class="recipient">Mr, Evan Marlow<br>President</p>

      <p class="recipient-company">Crestline Group<br>123 Street Name, Suite# 10<br>City, State, 120023</p>

      <h2 class="salutation">Dear Mr, Evan</h2>

      <p class="paragraph">Lorem ipsum dolor sit amet, consectetur adipiscing elit, sed do eiusmod tempor incididunt ut labore et dolore magna aliqua. Ut enim ad minim veniam, quis nostrud exercitation ullamco laboris nisi ut aliquip ex ea commodo consequat. Duis aute irure dolor in reprehenderit in voluptate velit esse cillum dolore eu fugiat nulla pariatur.</p>

      <p class="paragraph">Lorem ipsum dolor sit amet, consectetur adipiscing elit, sed do eiusmod tempor incididunt ut labore et dolore magna aliqua. Ut enim ad minim veniam, quis nostrud exercitation ullamco laboris nisi ut aliquip ex ea commodo consequat. Duis aute irure dolor in reprehenderit in voluptate velit esse cillum dolore eu fugiat nulla pariatur.</p>

      <p class="paragraph">Lorem ipsum dolor sit amet, consectetur adipiscing elit, sed do eiusmod tempor incididunt ut labore et dolore magna aliqua. Ut enim ad minim veniam, quis nostrud exercitation ullamco laboris nisi ut aliquip ex ea commodo consequat.</p>

      <p class="paragraph">Excepteur sint occaecat cupidatat non proident, sunt in culpa qui officia deserunt mollit anim id est laborum. re et dolore magnam aliquam quaerat voluptatem.</p>

      <p class="closing">Regards</p>

      <p class="signature">Dana Whitfield</p>
    </section>

    <svg class="footer-band" viewBox="0 0 764 20" aria-label="Phone 555.382.6519">
      <polygon points="0,0 443,0 428,20 0,20" fill="var(--brand-orange)"/>
      <polygon points="450,0 600,0 585,20 435,20" fill="var(--brand-grey)"/>
      <polygon points="607,0 764,0 764,20 592,20" fill="var(--brand-orange)"/>
      <text class="footer-phone" x="517" y="14.5" text-anchor="middle">555.382.6519</text>
    </svg>
  </main>
</body>
</html>
```